Home Page Website Design

The Site width is 1000 px. I've attached a Balsamiq mockup as a design layout guide. The design needs to be flat and clean. Please stick to the pixel dimensions of the mock up as the site will be responsive. I've also attached the logos used on the mockup for positional purposes.

Colours to use: Black, Grey, Green (Logo tie in) & green complementary colours.

Green (Logo tie in)
White Background
Titles: Black (Roboto Bold 700)
Text: Dark Grey (Roboto Normal 400)

Look & Style Example
http://www.brindlowe.org.uk/

Type Face
Google Fonts - Roboto

These are just guidelines, please feel free to use you own creative judgment.

Thanks

```html
<!DOCTYPE html>
<html lang="en">
<head>
<meta charset="utf-8">
<title>Ridgefield Teaching School Alliance – Home</title>
<link href="https://fonts.googleapis.com/css2?family=Roboto:wght@400;500;700&family=Roboto+Condensed:wght@400;700&display=swap" rel="stylesheet">
<style>
:root{
  --green:#0c9b48;
  --green-light:#16ad55;
  --green-dark:#07833a;
  --blue:#1f5c99;
  --blue-dark:#174a7e;
  --ink:#222;
  --text:#555;
  --muted:#777;
  --line:#d8d8d8;
  --band:#f1f1f1;
  --white:#fff;
}
*{box-sizing:border-box;margin:0;padding:0}
html,body{width:960px;height:1200px;overflow:hidden;background:var(--white)}
body{position:relative;font-family:'Roboto',sans-serif;color:var(--text)}
.abs{position:absolute}
.cond{font-family:'Roboto Condensed',sans-serif}

/* header */
.brand{left:82px;top:22px;width:200px}
.brand-mark{display:flex;align-items:center;gap:8px}
.brand-mark .square{width:30px;height:30px;background:var(--green)}
.brand-mark .name{font-family:'Roboto Condensed',sans-serif;font-weight:700;font-size:38px;color:var(--green);letter-spacing:1px}
.brand-sub{margin-top:18px;font-size:12px;color:var(--green)}
.login{left:821px;top:17px;width:50px;height:26px;background:#222;color:#fff;font:500 12px 'Roboto Condensed',sans-serif;display:flex;align-items:center;justify-content:center;border:1px solid #000}
.live-chat{left:487px;top:68px;width:114px;height:37px;background:linear-gradient(var(--green-light),var(--green-dark));display:flex;align-items:center;gap:8px;padding-left:12px;color:#fff;font:700 17px 'Roboto Condensed',sans-serif}
.register{left:613px;top:54px;width:266px;height:66px;border:1px solid #e3e3e3}
.register h3{position:absolute;left:9px;top:9px;font:700 14px 'Roboto Condensed',sans-serif;color:var(--green)}
.register .email{position:absolute;left:8px;top:31px;width:186px;height:27px;border:1px solid #ddd;font-size:8.5px;color:#888;padding:9px 7px}
.register .submit{position:absolute;left:200px;top:31px;width:57px;height:27px;background:#222;color:#fff;font:500 12px 'Roboto Condensed',sans-serif;display:flex;align-items:center;justify-content:center}

/* nav */
.nav{left:79px;top:129px;width:800px;height:33px;background:linear-gradient(#2567aa,var(--blue-dark));display:flex;align-items:center;padding-left:12px}
.nav a{color:#fff;text-decoration:none;font:700 9.5px 'Roboto Condensed',sans-serif;margin-right:22px}
.nav .search{position:absolute;left:613px;top:2px;width:184px;height:28px;background:#fff;font-size:8.5px;color:#999;padding:9px 4px}

/* hero */
.hero-panel{left:79px;top:170px;width:273px;height:272px;background:var(--green);color:#fff;padding:22px 12px 0 13px}
.hero-panel h1{font:700 18px 'Roboto Condensed',sans-serif;margin-bottom:11px}
.hero-panel p{font-size:11px;line-height:13.6px;text-align:justify;margin-bottom:13px}
.btn-find{left:93px;top:392px;width:135px;height:33px;background:var(--green-light);box-shadow:0 1px 3px rgba(0,0,0,.3);color:#fff;font:700 17px 'Roboto Condensed',sans-serif;display:flex;align-items:center;justify-content:center}
.dots{left:303px;top:410px;display:flex;gap:5px}
.dots span{width:7px;height:7px;border-radius:50%;background:#cfd8d3}
.dots span:first-child{background:#555}
.hero-photo{left:352px;top:170px;width:527px;height:272px;background:linear-gradient(135deg,#a8b0a6,#6f7d6c 50%,#c9bfa8)}

/* columns */
.col-title{font:700 17px 'Roboto Condensed',sans-serif;color:var(--green)}
.divider-v{width:1px;background:#e0e0e0}
.body-copy{font-size:10.5px;line-height:14.4px;text-align:justify;color:var(--text)}
.welcome-photo{left:79px;top:510px;width:249px;height:135px;background:linear-gradient(135deg,#c7c2b3,#8d8a7c 55%,#a4b06a)}
.td-list{left:356px;top:510px;width:247px}
.td-btn{height:31px;margin-bottom:2.6px;background:linear-gradient(var(--green-light),var(--green-dark));color:#fff;font:700 14px 'Roboto Condensed',sans-serif;display:flex;align-items:center;justify-content:space-between;padding:0 9px}
.item-title{font:500 11.5px 'Roboto',sans-serif;color:var(--ink);margin-bottom:1px}
.course{left:631px;width:248px;border-bottom:1px solid var(--line);height:117px}
.course .item-title{text-align:justify;line-height:14.4px}
.course .places{position:absolute;left:0;top:72px;font-size:10.5px}
.course .book{position:absolute;left:112px;top:62px;width:66px;height:21px;background:linear-gradient(var(--green-light),var(--green-dark));color:#fff;font:500 11px 'Roboto',sans-serif;display:flex;align-items:center;justify-content:center}

/* footer */
.footer-band{left:0;top:886px;width:960px;height:109px;background:var(--band)}
.footer-text{font:400 8.7px/11.4px 'Roboto Condensed',sans-serif;color:#555}
.follow{left:705px;top:903px;font:400 14px 'Roboto Condensed',sans-serif;color:#555}
.social{width:22px;height:22px;background:var(--blue)}
.social.alt{background:#2aa3e2}
.badge{left:734px;top:932px;width:68px;height:44px;background:#fff;border-radius:3px}
.badge::before{content:"";position:absolute;left:8px;top:8px;width:14px;height:28px;background:#9acd32;border-radius:7px}
.partners-title{left:0;top:1015px;width:960px;text-align:center;font:400 18px 'Roboto Condensed',sans-serif;color:#555}
.partner{background:#d6dde6}
.bottom-line{left:80px;top:1160px;width:800px;height:1px;background:#ddd}
.copyright{left:0;top:1172px;width:960px;text-align:center;font:400 10.5px 'Roboto Condensed',sans-serif;color:#555}
</style>
</head>
<body>

<header>
  <div class="abs brand">
    <div class="brand-mark"><span class="square"></span><span class="name">RTSA</span></div>
    <div class="brand-sub">Ridgefield Teaching School Alliance</div>
  </div>
  <div class="abs login">LOGIN</div>
  <div class="abs live-chat">
    <svg width="16" height="20" viewBox="0 0 16 20"><circle cx="8" cy="5" r="4.5" fill="#222"/><path d="M0 20c0-6 3.5-9 8-9s8 3 8 9z" fill="#222"/></svg>
    LIVE CHAT
  </div>
  <form class="abs register">
    <h3>REGISTER NOW!</h3>
    <div class="email">ENTER EMAIL ADDRESS</div>
    <div class="submit">SUBMIT</div>
  </form>
  <nav class="abs nav">
    <a>HOME</a><a>ABOUT US</a><a>TRAINING &amp; DEVELOPMENT</a><a>BENEFITS</a><a>MEMBERS</a><a>WHAT'S ON</a><a>CONTACT US</a><a>NEWS</a><a>FORUM</a>
    <div class="search">SEARCH..
      <svg class="abs" style="left:162px;top:7px" width="14" height="14" viewBox="0 0 14 14"><circle cx="5.5" cy="5.5" r="4" fill="none" stroke="#bbb" stroke-width="1.6"/><path d="M8.5 8.5l4.5 4.5" stroke="#bbb" stroke-width="2"/></svg>
    </div>
  </nav>
</header>

<section>
  <div class="abs hero-panel">
    <h1>NEW TEACHERS IN WORKSHOPS</h1>
    <p>Sedut perspiciatis unde omnis iste natus error sit voluptatem accusantium doloremque laudantium, totam rem aperiam, eaque ipsa quae ab illo inventore veritatis et quasi architecto beatae vitae dicta sunt explicabo.</p>
    <p>Nemo enim ipsam voluptatem quia voluptas sit aspernatur aut odit aut fugit, sed quia consequuntur magni dolores eos qui ratione voluptatem sequi nesciunt. Neque porro quisquam est, qui dolorem ipsum quia dolor sit amet, consectetur, adipisci velit.</p>
  </div>
  <div class="abs btn-find">FIND OUT MORE</div>
  <div class="abs dots"><span></span><span></span><span></span></div>
  <div class="abs hero-photo" role="img" aria-label="Teachers smiling and working on worksheets together at a workshop table"></div>
</section>

<main>
  <h2 class="abs col-title" style="left:80px;top:474px">WELCOME!</h2>
  <div class="abs welcome-photo" role="img" aria-label="Classroom of teachers seated at tables during a training session"></div>
  <div class="abs body-copy" style="left:79px;top:652px;width:249px">
    <p style="margin-bottom:14px">ed ut perspiciatis unde omnis iste natus error sit voluptatem accusantium doloremque laudantium, totam rem aperiam, eaque ipsa quae ab illo inventore veritatis et quasi architecto beatae vitae dicta sunt explicabo.</p>
    <p>Nemo enim ipsam voluptatem quia voluptas sit aspernatur aut odit aut fugit, sed quia consequuntur magni dolores eos qui ratione voluptatem sequi nesciunt. Neque porro quisquam est, qui dolorem ipsum quia dolor sit amet, consectetur, adipisci velit, sed quia non numquam eius modi tempora incidunt ut labore et dolore magnam aliquam quaerat voluptatem. Ut enim ad minima veniam,</p>
  </div>
  <div class="abs divider-v" style="left:341px;top:474px;height:384px"></div>

  <h2 class="abs col-title" style="left:356px;top:474px">TRAINING &amp; DEVELOPMENT</h2>
  <div class="abs td-list">
    <div class="td-btn">LEADERSHIP TRAINING<svg width="18" height="10" viewBox="0 0 18 10"><path d="M1 1l4 4-4 4M7 1l4 4-4 4" fill="none" stroke="#fff" stroke-width="2"/></svg></div>
    <div class="td-btn">CPD<svg width="18" height="10" viewBox="0 0 18 10"><path d="M1 1l4 4-4 4M7 1l4 4-4 4" fill="none" stroke="#fff" stroke-width="2"/></svg></div>
    <div class="td-btn">SCHOOL 2 SCHOOL SUPPORT<svg width="18" height="10" viewBox="0 0 18 10"><path d="M1 1l4 4-4 4M7 1l4 4-4 4" fill="none" stroke="#fff" stroke-width="2"/></svg></div>
    <div class="td-btn">RESEARCH &amp; DEVELOPMENT<svg width="18" height="10" viewBox="0 0 18 10"><path d="M1 1l4 4-4 4M7 1l4 4-4 4" fill="none" stroke="#fff" stroke-width="2"/></svg></div>
    <div class="td-btn">ITT (SCHOOL DIRECT)<svg width="18" height="10" viewBox="0 0 18 10"><path d="M1 1l4 4-4 4M7 1l4 4-4 4" fill="none" stroke="#fff" stroke-width="2"/></svg></div>
  </div>
  <h2 class="abs col-title" style="left:357px;top:691px">LATEST NEWS</h2>
  <article class="abs" style="left:355px;top:724px;width:249px">
    <h4 class="item-title">Lorem ut perspiciatis unde omnis</h4>
    <p class="body-copy">iste natus error sit voluptatem accusantium doloremque laudantium, totam rem aperiam, eaque ipsa quae ab illo inventore</p>
  </article>
  <article class="abs" style="left:355px;top:796px;width:249px">
    <h4 class="item-title">Lorem ut perspiciatis unde omnis</h4>
    <p class="body-copy">iste natus error sit voluptatem accusantium doloremque laudantium, totam rem aperiam, eaque ipsa quae ab illo inventore</p>
  </article>
  <div class="abs divider-v" style="left:617px;top:474px;height:384px"></div>

  <h2 class="abs col-title" style="left:632px;top:474px">LATEST COURSES</h2>
  <article class="abs course" style="top:512px">
    <h4 class="item-title">Want to Deliver consistently 'Outstanding' Lessons?</h4>
    <p class="body-copy">iste natus error sit voluptatem accusantium doloremque laudantium, totam rem aperiam,</p>
    <span class="places">6 Places Left</span><span class="book">Book Now!</span>
  </article>
  <article class="abs course" style="top:630px">
    <h4 class="item-title">School Direct Initial Teacher Training Places Still available</h4>
    <p class="body-copy">iste natus error sit voluptatem accusantium doloremque laudantium, totam rem aperiam,</p>
    <span class="places">6 Places Left</span><span class="book">Book Now!</span>
  </article>
  <article class="abs course" style="top:748px">
    <h4 class="item-title">Want to Deliver consistently 'Outstanding' Lessons?</h4>
    <p class="body-copy">iste natus error sit voluptatem accusantium doloremque laudantium, totam rem aperiam,</p>
    <span class="places">6 Places Left</span><span class="book">Book Now!</span>
  </article>
</main>

<footer>
  <div class="abs footer-band"></div>
  <div class="abs footer-text" style="left:104px;top:905px">Ridgefield Teaching Schools Alliance<br>Meadow Lane<br>Ashbury, AB1 2CD<br><span style="display:block;margin-top:4px">Tel:01632 960000</span>Email : info@ridgefieldteaching.co.uk</div>
  <div class="abs divider-v" style="left:294px;top:890px;height:92px;background:#d0d0d0"></div>
  <div class="abs footer-text" style="left:338px;top:905px;line-height:14.4px">About Us<br>Training &amp; Development<br>Benefits<br>Members<br>Calendar of Events</div>
  <div class="abs footer-text" style="left:529px;top:905px;line-height:14.4px">Contact Us<br>News<br>Forum<br>Site map</div>
  <div class="abs divider-v" style="left:662px;top:890px;height:92px;background:#d0d0d0"></div>
  <div class="abs follow">FOLLOW US</div>
  <div class="abs social" style="left:789px;top:900px"></div>
  <div class="abs social alt" style="left:816px;top:900px"></div>
  <div class="abs badge"></div>

  <h2 class="abs partners-title">PARTNER SCHOOLS</h2>
  <div class="abs partner" style="left:86px;top:1060px;width:34px;height:40px;border-radius:0 0 17px 17px"></div>
  <div class="abs partner" style="left:132px;top:1060px;width:50px;height:40px;border-radius:50%;background:#f08a5d"></div>
  <div class="abs partner" style="left:208px;top:1064px;width:112px;height:54px;background:#e6ebf3"></div>
  <div class="abs partner" style="left:348px;top:1062px;width:60px;height:62px;background:#1e2f9c"></div>
  <div class="abs partner" style="left:456px;top:1060px;width:46px;height:50px;border-radius:0 0 23px 23px;background:#1c3c7a"></div>
  <div class="abs partner" style="left:546px;top:1058px;width:42px;height:52px;border-radius:0 0 21px 21px;background:#8a5aa8"></div>
  <div class="abs partner" style="left:630px;top:1064px;width:36px;height:44px;border-radius:0 0 18px 18px;background:#c9a227"></div>
  <div class="abs partner" style="left:711px;top:1058px;width:42px;height:80px;border-radius:0 0 21px 21px;background:#b23a48"></div>
  <div class="abs partner" style="left:792px;top:1062px;width:72px;height:80px;border-radius:50%;background:#2a4fa0"></div>
  <div class="abs bottom-line"></div>
  <div class="abs copyright">©&nbsp; Ridgefield Teaching Schools Alliance</div>
</footer>

</body>
</html>
```